A NEW UPDATED VERSION OF A 4"X9" RACK CARD

A NEW UPDATED VERSION OF A RACK CARD, THIS CARD IS 5 YEARS OLD AND WE WANT SOMETHING NEW AND FRESH AND MORE UPDATED TO TODAY. MARKET TO A YOUNGER CROWD. USE THE ATTACHED RACK CARD FOR THE INFO AND VERBAGE AND LOGO TO BE USED. DO NOT USE THE PICTURE OF THE BUILDIING, don't use the picture of the 2 guys. USED THE ATTACHED POST CARDS AS COLORS AND REFERENCE.

Target Market(s)

25-45

Industry/Entity Type

HOME INSPECTIONS

```html
<!DOCTYPE html>
<html lang="en">
<head>
<meta charset="utf-8">
<title>Liberty Ridge Home Inspections – Rack Card</title>
<link href="https://fonts.googleapis.com/css2?family=Montserrat:wght@400;500;600;700;800;900&display=swap" rel="stylesheet">
<style>
  :root {
    --page-bg: #d9d9d9;
    --card-white: #fbfbfb;
    --navy: #1f3d99;
    --blue: #2c4fb8;
    --red: #e3303b;
    --yellow: #f2e23a;
    --ink: #3a3d45;
    --steel-light: #eeeff0;
    --steel-mid: #d4d6d8;
    --logo-ink: #2a2f4a;
  }
  * { box-sizing: border-box; margin: 0; padding: 0; }
  html, body {
    width: 1200px; height: 800px; overflow: hidden;
    background: var(--page-bg);
    font-family: "Montserrat", sans-serif;
  }
  .rack-card {
    position: absolute; left: 430px; top: 17px;
    width: 340px; height: 765px;
    background: var(--card-white);
    overflow: hidden;
    box-shadow: 0 6px 18px rgba(0,0,0,0.18);
  }
  .plate-texture {
    position: absolute; left: 0; top: 0; width: 340px; height: 240px;
    background: linear-gradient(160deg, var(--steel-light), var(--steel-mid));
  }
  .brand-lockup {
    position: absolute; left: 0; top: 70px; width: 340px;
    display: flex; align-items: center; justify-content: center; gap: 10px;
  }
  .brand-mark {
    width: 38px; height: 38px; border-radius: 50%;
    background: var(--red); flex: none;
  }
  .brand-name {
    font-weight: 800; font-size: 19px; line-height: 1.1;
    color: var(--logo-ink); text-transform: uppercase; letter-spacing: 0.5px;
  }
  .hero-band { position: absolute; left: 0; top: 200px; width: 340px; height: 190px; }
  .hero-copy { position: absolute; left: 22px; top: 300px; color: #fff; }
  .hero-title { font-weight: 800; font-size: 15px; letter-spacing: 0.6px; }
  .hero-tagline { font-weight: 500; font-size: 7.5px; letter-spacing: 0.5px; line-height: 1.3; margin-top: 3px; }
  .rank { display: flex; align-items: center; gap: 10px; margin-top: 6px; }
  .rank-title { font-weight: 800; font-size: 11px; color: var(--yellow); }
  .rank-sub { font-weight: 500; font-size: 6.5px; letter-spacing: 0.4px; }
  .rank-badge { width: 22px; height: 22px; border-radius: 50%; background: var(--yellow); }
  .why-us { position: absolute; left: 22px; top: 392px; width: 300px; color: var(--ink); }
  .why-title { font-weight: 900; font-size: 24px; color: var(--navy); letter-spacing: 0.5px; }
  .why-intro { font-size: 8px; line-height: 1.4; margin-top: 4px; }
  .benefit-list { list-style: none; margin-top: 8px; }
  .benefit-list li {
    position: relative; padding-left: 18px;
    font-size: 8px; line-height: 1.4; margin-bottom: 7px;
  }
  .tick { position: absolute; left: 0; top: 10px; width: 8px; height: 8px; }
  .stripe-red { position: absolute; left: 0; top: 628px; width: 340px; height: 28px; background: var(--red); }
  .stripe-blue {
    position: absolute; left: 0; top: 690px; width: 340px; height: 75px;
    background: var(--blue); color: #fff;
    display: flex; align-items: center; justify-content: center; text-align: center;
    padding: 0 24px; font-size: 8px; line-height: 1.45; font-weight: 500;
  }
  .action-row {
    position: absolute; left: 22px; top: 612px; width: 296px;
    display: flex; justify-content: space-between;
  }
  .action-box {
    width: 140px; height: 64px; background: #fff;
    border: 1.5px solid var(--red);
    display: flex; flex-direction: column; align-items: center; justify-content: center;
    text-align: center;
  }
  .action-icon { width: 20px; height: 20px; margin-bottom: 3px; }
  .action-title { font-weight: 700; font-size: 8.5px; color: var(--ink); }
  .action-sub { font-size: 6.5px; color: var(--ink); margin-top: 1px; }
</style>
</head>
<body>
  <main class="rack-card">
    <div class="plate-texture" role="img" aria-label="Brushed diamond-plate steel texture background"></div>

    <div class="brand-lockup">
      <span class="brand-mark"></span>
      <span class="brand-name">Liberty Ridge<br>Home Inspections</span>
    </div>

    <svg class="hero-band" viewBox="0 0 340 190" aria-hidden="true">
      <path d="M0,80 L316,0 C288,70 262,128 212,158 C150,186 80,188 0,190 Z" fill="var(--blue)"/>
      <path d="M324,0 L340,0 L340,62 C300,86 262,124 222,156 C270,120 298,64 324,0 Z" fill="var(--red)"/>
    </svg>

    <div class="hero-copy">
      <h1 class="hero-title">LIBERTY RIDGE INSPECTION</h1>
      <p class="hero-tagline">PROFESSIONAL &amp; PROMPT SERVICE<br>GUARANTEED</p>
      <div class="rank">
        <div>
          <p class="rank-title">FLORIDA'S #1</p>
          <p class="rank-sub">INSPECTION COMPANY</p>
        </div>
        <span class="rank-badge"></span>
      </div>
    </div>

    <section class="why-us">
      <h2 class="why-title">WHY US?</h2>
      <p class="why-intro">Liberty Ridge Home Inspections strives to provide the absolute best home inspection experience for each and every customer</p>
      <ul class="benefit-list">
        <li><svg class="tick" viewBox="0 0 10 10"><path d="M1,5 L4,8 L9,2" fill="none" stroke="var(--red)" stroke-width="1.8"/></svg>All Liberty Ridge Home Inspections Inspectors are trained to the highest standards in the industry and are equipped with the most advanced tools to ensure all customers are getting a great inspection as well as getting a great value.</li>
        <li><svg class="tick" viewBox="0 0 10 10"><path d="M1,5 L4,8 L9,2" fill="none" stroke="var(--red)" stroke-width="1.8"/></svg>Our full Home Inspections include a comprehensive visual inspection of the interior and exterior of the home looking at over 1,400 different items.</li>
        <li><svg class="tick" viewBox="0 0 10 10"><path d="M1,5 L4,8 L9,2" fill="none" stroke="var(--red)" stroke-width="1.8"/></svg>We inspect and test all accesible components of the home, inputting our findings into a report that is honest and easy to understand and full of pictures for easy reference</li>
        <li><svg class="tick" viewBox="0 0 10 10"><path d="M1,5 L4,8 L9,2" fill="none" stroke="var(--red)" stroke-width="1.8"/></svg>We base our pricing on total square footage of the home and do not charge extra to inspect pools, attics, roofs, or crawlspaces</li>
      </ul>
    </section>

    <div class="stripe-red"></div>

    <div class="action-row">
      <div class="action-box">
        <svg class="action-icon" viewBox="0 0 20 20" aria-hidden="true">
          <circle cx="10" cy="10" r="8.5" fill="none" stroke="var(--red)" stroke-width="1.6"/>
          <ellipse cx="10" cy="10" rx="4" ry="8.5" fill="none" stroke="var(--red)" stroke-width="1.2"/>
          <line x1="1.5" y1="10" x2="18.5" y2="10" stroke="var(--red)" stroke-width="1.2"/>
        </svg>
        <p class="action-title">Visit our Website</p>
        <p class="action-sub">to Book an Inspection</p>
      </div>
      <div class="action-box">
        <svg class="action-icon" viewBox="0 0 20 20" aria-hidden="true">
          <circle cx="10" cy="10" r="8.5" fill="var(--red)"/>
        </svg>
        <p class="action-title">Friendly Inspector</p>
        <p class="action-sub">Your honest and friendly inspector</p>
      </div>
    </div>

    <footer class="stripe-blue">
      <p>WDO (Termite inspections) performed by Bright Shield Pest Care and is included with every full home inspection</p>
    </footer>
  </main>
</body>
</html>
```